Re-design and craft the perfect CV platform

We are building a CV-based platform designed to connect employees and employers, with a strong focus on individual users. As we're just starting out, we're looking to have our platform and logo redesigned to better reflect our vision
https://app.zelvorhire.com/
Colors like in the logo attached
#87C032 #6A6E71 #618930 - also you can add more colors if you like.
https://app.zelvorhire.com/dashboard - This page would be nice if you plan it, like personal Bio dashboard. Attached picture (Dashboard wanted) one idea from how we would like to be, but we are open for new professional ideas/solutions.
https://app.zelvorhire.com/posts - On this page we want to be showed the jobs posted. Attached one picture about our idea (jobs page wanted)
https://app.zelvorhire.com/profile - design something nice.
Only Photoshop, Illustrator or Interface Design
Other pictures from the app attached (as looking right now)

Target Market(s)

Job seekers, HR, Recruiters

Industry/Entity Type

HR Tech

Number of Pages Required

5+ page

Colors
00AB8E
00BBA5
67D7C9
C6EFE9
E9F9F6

```html
<!DOCTYPE html>
<html lang="en">
<head>
<meta charset="utf-8">
<title>Zelvor – Recruitment web app screens</title>
<link href="https://fonts.googleapis.com/css2?family=Poppins:wght@400;500;600;700&display=swap" rel="stylesheet">
<style>
:root{
  --green:#87c032;
  --green-dk:#618930;
  --green-lt:#e6f3d3;
  --grey:#6a6e71;
  --grey-lt:#a4a8ab;
  --line:#e4e6e8;
  --panel:#f1f2f3;
  --ink:#2d3033;
  --red:#e8707a;
  --stage-top:#2c4d12;
  --stage-bot:#6ea33a;
  --band:#1d360b;
}
*{box-sizing:border-box;margin:0;padding:0}
html,body{width:1200px;height:4073px;overflow:hidden}
body{font-family:"Poppins",sans-serif;color:var(--ink);background:var(--band);position:relative}
.stage{position:absolute;left:0;top:0;width:1200px;height:2560px;background:linear-gradient(180deg,var(--stage-top) 0%,#4e7f25 55%,var(--stage-bot) 100%);overflow:hidden}
.ghost-word{position:absolute;font-weight:700;color:rgba(255,255,255,.06);letter-spacing:8px;line-height:1}
.screen{position:absolute;left:80px;width:1040px;height:586px;background:var(--panel);overflow:hidden;box-shadow:0 20px 40px rgba(0,0,0,.25)}
.brand{display:flex;align-items:center;gap:6px;font-weight:700;color:var(--green-dk);letter-spacing:1px}
.brand .dot{width:14px;height:14px;border-radius:50%;background:var(--green)}

/* login */
.login{top:180px;background:#f4f5f3}
.login .hill{position:absolute;left:0;bottom:0;width:1040px;height:170px}
.login-card{position:absolute;left:105px;top:92px;width:379px;height:405px;background:#fff;border-radius:6px;box-shadow:0 6px 20px rgba(0,0,0,.08);text-align:center;padding-top:28px}
.login-card .brand{justify-content:center;font-size:22px}
.login-card h1{font-size:21px;font-weight:600;margin-top:26px}
.login-card .sub{font-size:10.5px;color:var(--grey);margin-top:8px}
.login-form{margin:22px 16px 0;background:var(--panel);border-radius:4px;padding:20px 18px 24px;text-align:left}
.login-form label{font-size:11px;font-weight:600}
.input{margin-top:12px;height:38px;background:#fff;border-radius:4px;display:flex;align-items:center;gap:12px;padding:0 14px;font-size:10.5px;color:var(--grey-lt)}
.btn-green{background:var(--green);color:#fff;font-weight:600;border-radius:4px;text-align:center}
.login-form .btn-green{margin-top:22px;height:42px;line-height:42px;font-size:16px}
.illus{position:absolute;left:509px;top:139px;width:492px;height:317px;border-radius:8px;background:linear-gradient(135deg,#cfe6ad,#8fc448 60%,#dfe3e0)}

/* app chrome */
.nav{height:62px;background:#fff;display:flex;align-items:center;padding:0 28px;position:relative}
.nav .brand{font-size:17px}
.tabs{position:absolute;left:330px;top:0;height:62px;display:flex;align-items:flex-end;gap:4px}
.tab{height:46px;padding:0 28px;display:flex;align-items:center;gap:7px;font-size:13px;color:var(--grey);border-radius:12px 12px 0 0}
.tab.active{background:var(--green-lt);color:var(--green-dk);font-weight:500}
.tab i{width:9px;height:9px;border-radius:2px;background:currentColor;display:inline-block}
.nav-icons{margin-left:auto;display:flex;gap:14px;align-items:center}
.avatar-sm{width:28px;height:28px;border-radius:50%;background:linear-gradient(#8fb6d8,#3a5a78)}
.icon-dot{width:15px;height:15px;border-radius:4px;background:var(--green)}
.app{top:966px}
.jobs-screen{top:1752px}
.card{position:absolute;background:#fff;border-radius:6px}

/* profile */
.profile{left:27px;top:83px;width:213px;height:476px;padding:18px 16px;text-align:center;font-size:8.5px;color:var(--grey)}
.avatar{width:52px;height:52px;border-radius:50%;background:linear-gradient(#a7c6e2,#45658a);margin:0 auto}
.profile .name{font-size:11px;font-weight:600;color:var(--ink);margin-top:8px}
.profile .role{font-size:7.5px;letter-spacing:.5px}
.meta{display:flex;justify-content:space-between;margin:14px 10px 0}
.meta b{display:block;color:var(--green);font-weight:500;margin-bottom:6px}
.sec-title{font-size:9px;font-weight:600;color:var(--ink);margin:18px 0 10px}
.contact{display:flex;gap:10px;text-align:left;align-items:center;margin-bottom:10px}
.contact .ic{width:20px;height:20px;border-radius:4px;background:var(--green-lt);flex:none}
.contact b{display:block;color:var(--green);font-weight:500}
.langs{display:flex;justify-content:space-around}
.lang svg{display:block;margin:0 auto 4px}
.licence{display:flex;gap:10px;text-align:left;font-size:7.5px}
.licence b{display:block;color:var(--ink);font-weight:600;margin-bottom:3px}

/* middle */
.mid{left:265px;top:83px;width:513px;height:476px;padding:18px 18px;font-size:8px;color:var(--grey)}
.mid h2{font-size:13px;font-weight:600;color:var(--ink)}
.head-row{display:flex;justify-content:space-between;align-items:center}
.pill{background:var(--green);color:#fff;border-radius:3px;padding:2px 6px;font-size:8px;font-weight:600;margin-left:6px}
.mid h3{font-size:8.5px;font-weight:600;color:var(--ink);margin:16px 0 8px}
.mid p{line-height:1.55;margin-bottom:7px}
.more{color:var(--green)}
.edu{display:flex;gap:30px}
.edu div{display:flex;gap:7px}
.edu i{width:14px;height:14px;border-radius:50%;background:var(--green-lt);flex:none}
.edu b{display:block;color:var(--ink);font-weight:600}
.work{display:grid;grid-template-columns:1fr 1fr;gap:8px 14px}
.work div{background:var(--panel);border-radius:4px;padding:7px 10px}
.work b{display:block;color:var(--ink);font-weight:600}

/* right */
.activity{left:803px;top:83px;width:214px;height:226px;padding:16px 14px;font-size:8px;color:var(--grey)}
.right-head{display:flex;justify-content:space-between;font-size:10px;font-weight:600;color:var(--ink)}
.right-head span{font-size:8px;font-weight:400;color:var(--green)}
.act{display:flex;gap:10px;align-items:center;margin-top:18px;border-left:2px solid var(--green);padding-left:6px}
.act .ic{width:22px;height:22px;border-radius:50%;flex:none}
.skills{left:803px;top:334px;width:214px;height:225px;padding:16px 14px;font-size:8px;color:var(--grey)}
.skills h4{text-align:center;font-size:9.5px;font-weight:600;color:var(--ink);margin-bottom:12px}
.skill{display:flex;align-items:center;height:20px}
.skill span{width:94px}
.bar{flex:1;height:5px;background:var(--line);border-radius:3px;margin-right:8px;position:relative}
.bar b{position:absolute;left:0;top:0;height:5px;border-radius:3px;background:var(--green)}

/* jobs */
.jobs-mid{padding:16px 16px}
.sort{display:flex;align-items:center;gap:6px;font-size:8px}
.sort .pill{padding:3px 10px;margin:0}
.sq{width:16px;height:16px;border-radius:3px;background:var(--green-lt);border:1px solid var(--green)}
.grid{position:absolute;left:16px;top:56px;width:368px;display:grid;grid-template-columns:1fr 1fr;gap:16px}
.job{border:1px solid var(--line);border-radius:5px;padding:10px 12px;height:196px}
.job .logo{width:16px;height:16px;border-radius:50%}
.job h5{font-size:11px;font-weight:500;color:var(--ink);margin-top:8px;line-height:1.3}
.stars{color:var(--green);font-size:10px;letter-spacing:1px;margin-top:3px}
.stars small{color:var(--grey-lt);font-size:7px;letter-spacing:0}
.tags{display:flex;gap:4px;margin-top:8px}
.tags span{border:1px solid var(--line);border-radius:8px;padding:1px 6px;font-size:6.5px}
.salary{display:flex;justify-content:space-between;align-items:baseline;margin-top:16px;font-size:7px}
.salary b{font-size:11px;color:var(--ink);font-weight:600}
.apply{margin-top:12px;height:18px;line-height:18px;font-size:7.5px}
.apply.off{background:#d6d8da;color:#fff}
.filter{position:absolute;left:392px;top:56px;width:108px;border-left:3px solid var(--green);padding-left:10px}
.filter .fh{display:flex;justify-content:space-between;font-size:9px;font-weight:600;color:var(--ink)}
.filter .fh span{font-weight:400;color:var(--green);font-size:7.5px}
.filter h6{font-size:8.5px;font-weight:500;color:var(--ink);margin:14px 0 4px}
.opt{display:flex;align-items:center;gap:5px;font-size:7px;height:15px}
.opt i{width:8px;height:8px;border-radius:2px;border:1px solid var(--grey-lt)}
.opt.on{color:var(--green)}
.opt.on i{background:var(--green);border-color:var(--green)}

.band-brand{position:absolute;left:0;top:2560px;width:1200px;height:300px;display:flex;justify-content:center;align-items:center}
.band-brand .brand{font-size:40px;color:#fff;gap:14px}
.band-brand .dot{width:30px;height:30px}
</style>
</head>
<body>
<div class="stage">
  <div class="ghost-word" style="left:1090px;top:230px;font-size:150px;writing-mode:vertical-rl">LOGIN</div>
  <div class="ghost-word" style="left:-10px;top:1060px;font-size:150px;writing-mode:vertical-rl;transform:rotate(180deg)">CV</div>
  <div class="ghost-word" style="left:60px;top:2370px;font-size:150px">JOB PORTAL</div>

  <!-- Login -->
  <section class="screen login">
    <svg class="hill" viewBox="0 0 1040 170" preserveAspectRatio="none"><path d="M0 100 C200 20 380 70 560 60 C760 50 900 10 1040 0 L1040 170 L0 170Z" fill="#8ec240"/><path d="M0 130 C220 70 420 110 620 95 C820 82 940 60 1040 50 L1040 170 L0 170Z" fill="#7fb436"/></svg>
    <div class="illus" role="img" aria-label="Illustration of two job seekers with magnifying glasses beside a large phone showing a job listing"></div>
    <div class="login-card">
      <div class="brand"><span class="dot"></span>ZELVOR</div>
      <h1>Recruitment web app access</h1>
      <p class="sub">Login to your account to continue</p>
      <div class="login-form">
        <label>Email Address</label>
        <div class="input"><svg width="11" height="9" viewBox="0 0 11 9"><rect x=".5" y=".5" width="10" height="8" rx="1" fill="none" stroke="#87c032"/><path d="M1 1l4.5 4 4.5-4" fill="none" stroke="#87c032"/></svg>Enter Email Address</div>
        <div class="btn-green">Login →</div>
      </div>
    </div>
  </section>

  <!-- CV -->
  <section class="screen app">
    <header class="nav">
      <div class="brand"><span class="dot"></span>ZELVOR</div>
      <nav class="tabs"><div class="tab"><i></i>Jobs</div><div class="tab active"><i></i>CV</div><div class="tab"><i></i>Notification</div></nav>
      <div class="nav-icons"><div class="avatar-sm" role="img" aria-label="User photo"></div><span class="icon-dot"></span><span class="icon-dot" style="border-radius:50%"></span><span class="icon-dot" style="border-radius:50%;background:var(--green-dk)"></span></div>
    </header>
    <aside class="card profile">
      <div class="avatar" role="img" aria-label="Profile photo"></div>
      <div class="name">Mirela Dascot</div><div class="role">UI/UX DESIGNER</div>
      <div class="meta"><div><b>Age</b>32 Year</div><div><b>Gender</b>Female</div></div>
      <div class="sec-title">Contact Info</div>
      <div class="contact"><span class="ic"></span><div><b>Email Address</b>info@mireladascot.com</div></div>
      <div class="contact"><span class="ic"></span><div><b>Phone Number</b>+1 555 010 4471</div></div>
      <div class="sec-title">Language</div>
      <div class="langs">
        <div class="lang"><svg width="34" height="34" viewBox="0 0 34 34"><circle cx="17" cy="17" r="13" fill="none" stroke="#e4e6e8" stroke-width="4"/><circle cx="17" cy="17" r="13" fill="none" stroke="#a4a8ab" stroke-width="4" stroke-dasharray="41 82" transform="rotate(-90 17 17)"/><text x="17" y="20" font-size="7" text-anchor="middle" fill="#6a6e71">50%</text></svg>English</div>
        <div class="lang"><svg width="34" height="34" viewBox="0 0 34 34"><circle cx="17" cy="17" r="13" fill="none" stroke="#e4e6e8" stroke-width="4"/><circle cx="17" cy="17" r="13" fill="none" stroke="#87c032" stroke-width="4" stroke-dasharray="41 82" transform="rotate(-90 17 17)"/><text x="17" y="20" font-size="7" text-anchor="middle" fill="#6a6e71">50%</text></svg>Spanish</div>
        <div class="lang"><svg width="34" height="34" viewBox="0 0 34 34"><circle cx="17" cy="17" r="13" fill="none" stroke="#e4e6e8" stroke-width="4"/><circle cx="17" cy="17" r="13" fill="none" stroke="#618930" stroke-width="4" stroke-dasharray="41 82" transform="rotate(-90 17 17)"/><text x="17" y="20" font-size="7" text-anchor="middle" fill="#6a6e71">50%</text></svg>Deutsch</div>
      </div>
      <div class="sec-title">Driver License</div>
      <div class="licence"><span class="contact"><span class="ic"></span></span><div><b>Driver's Licence Western Australia</b>Licence Number &nbsp;4321772<br>Expiry Date &nbsp;&nbsp;&nbsp;17 Jun 2026</div></div>
    </aside>
    <main class="card mid">
      <div class="head-row"><h2>Experience</h2><span>Years of work experience <span class="pill">15 years</span></span></div>
      <h3>About</h3>
      <p>I'm a Product Designer based in Melbourne, Australia. I enjoy working on product design and web builder projects. I occasionally take on freelance work.</p>
      <p>I've worked with some of the most exciting companies, including Northlane, Paycrest and Tallyform. I'm passionate about helping startups grow, improve their UX and customer experience, and to fundraise through good design.</p>
      <p>My work has been featured on Typeharbor, Brightfold Journal, Sitecraft Awards, Gridlist, Pixel Shelf and more galleries.</p>
      <span class="more">Read more</span>
      <h3>Education</h3>
      <div class="edu">
        <div><i></i><span><b>Course Studies (School)</b>Computer science<br>2003 – 2005</span></div>
        <div><i></i><span><b>Maplewood College</b>Studies of Business Management<br>2009 – 2011</span></div>
        <div><i></i><span><b>Maplewood University</b>Bachelor of Business Management<br>2011 – 2015</span></div>
      </div>
      <h3>Work Experience</h3>
      <div class="work">
        <div><b>Studio Veldmark Canberra Australia</b>Jr. Graphic Designer<br>2015 – 2016</div>
        <div><b>Digital Marketing Agency</b>Graphic Designer<br>2016 – 2018</div>
        <div><b>Orrin Co. Kota Baru – Singapore</b>UI/UX Designer<br>2018 – 2020</div>
        <div><b>Studio Veldmark Sydney Australia</b>Project Manager<br>2020 – 2024</div>
      </div>
      <p class="more" style="text-align:center;margin-top:10px">Read more</p>
    </main>
    <div class="card activity">
      <div class="right-head">Last Activites<span>See All</span></div>
      <div class="act"><span class="ic" style="background:#87c032"></span><span>Your Application has accept<br><b style="color:var(--ink);font-weight:500">3 Companies</b></span></div>
      <div class="act"><span class="ic" style="background:var(--red)"></span><span>Your Application has rejected<br><b style="color:var(--ink);font-weight:500">1 Companies</b></span></div>
    </div>
    <div class="card skills">
      <h4>Skills</h4>
      <div class="skill"><span>Photo Editing</span><div class="bar"><b style="width:87%"></b></div>87%</div>
      <div class="skill"><span>Vector Illustration</span><div class="bar"><b style="width:84%"></b></div>84%</div>
      <div class="skill"><span>Motion Graphics</span><div class="bar"><b style="width:55%"></b></div>55%</div>
      <div class="skill"><span>Video Editing</span><div class="bar"><b style="width:67%"></b></div>67%</div>
      <div class="skill"><span>Layout Design</span><div class="bar"><b style="width:48%"></b></div>48%</div>
      <div class="skill"><span>Prototyping</span><div class="bar"><b style="width:90%"></b></div>90%</div>
      <div class="skill"><span>Interface Design</span><div class="bar"><b style="width:31%"></b></div>31%</div>
      <div class="skill"><span>Office Suite</span><div class="bar"><b style="width:54%"></b></div>54%</div>
    </div>
  </section>

  <!-- Jobs -->
  <section class="screen jobs-screen">
    <header class="nav">
      <div class="brand"><span class="dot"></span>ZELVOR</div>
      <nav class="tabs"><div class="tab active"><i></i>Jobs</div><div class="tab"><i></i>CV</div><div class="tab"><i></i>Notification</div></nav>
      <div class="nav-icons"><div class="avatar-sm" role="img" aria-label="User photo"></div><span class="icon-dot"></span><span class="icon-dot" style="border-radius:50%"></span><span class="icon-dot" style="border-radius:50%;background:var(--green-dk)"></span></div>
    </header>
    <aside class="card profile">
      <div class="avatar" role="img" aria-label="Profile photo"></div>
      <div class="name">Mirela Dascot</div><div class="role">UI/UX DESIGNER</div>
      <div class="meta"><div><b>Age</b>32 Year</div><div><b>Gender</b>Female</div></div>
      <div class="sec-title">Contact Info</div>
      <div class="contact"><span class="ic"></span><div><b>Email Address</b>info@mireladascot.com</div></div>
      <div class="contact"><span class="ic"></span><div><b>Phone Number</b>+1 555 010 4471</div></div>
      <div class="sec-title">Language</div>
      <div class="langs">
        <div class="lang"><svg width="34" height="34" viewBox="0 0 34 34"><circle cx="17" cy="17" r="13" fill="none" stroke="#e4e6e8" stroke-width="4"/><circle cx="17" cy="17" r="13" fill="none" stroke="#a4a8ab" stroke-width="4" stroke-dasharray="41 82" transform="rotate(-90 17 17)"/><text x="17" y="20" font-size="7" text-anchor="middle" fill="#6a6e71">50%</text></svg>English</div>
        <div class="lang"><svg width="34" height="34" viewBox="0 0 34 34"><circle cx="17" cy="17" r="13" fill="none" stroke="#e4e6e8" stroke-width="4"/><circle cx="17" cy="17" r="13" fill="none" stroke="#87c032" stroke-width="4" stroke-dasharray="41 82" transform="rotate(-90 17 17)"/><text x="17" y="20" font-size="7" text-anchor="middle" fill="#6a6e71">50%</text></svg>Spanish</div>
        <div class="lang"><svg width="34" height="34" viewBox="0 0 34 34"><circle cx="17" cy="17" r="13" fill="none" stroke="#e4e6e8" stroke-width="4"/><circle cx="17" cy="17" r="13" fill="none" stroke="#618930" stroke-width="4" stroke-dasharray="41 82" transform="rotate(-90 17 17)"/><text x="17" y="20" font-size="7" text-anchor="middle" fill="#6a6e71">50%</text></svg>Deutsch</div>
      </div>
      <div class="sec-title">Driver License</div>
      <div class="licence"><span class="contact"><span class="ic"></span></span><div><b>Driver's Licence Western Australia</b>Licence Number &nbsp;4321772<br>Expiry Date &nbsp;&nbsp;&nbsp;17 Jun 2026</div></div>
    </aside>
    <main class="card mid jobs-mid">
      <div class="head-row"><h2>Total jobs <span style="font-size:7px;font-weight:400;border:1px solid var(--line);border-radius:3px;padding:1px 5px;color:var(--grey)">115 Found</span></h2>
        <div class="sort">Sort by: <span class="pill">Urgently hiring ⌄</span><span class="icon-dot"></span><span class="sq"></span></div></div>
      <div class="grid">
        <div class="job"><span class="logo" style="display:block;background:#e8a23a"></span><h5>Senior UI/UX<br>Designer</h5><div class="stars">★★★★☆ <small>(42 Reviews)</small></div><div style="font-size:7px;margin-top:3px">● California, CA</div><div class="tags"><span>Full Time</span><span>Senior Level</span><span>Remote</span></div><div class="salary"><span><b>$2.5k</b>/Monthly</span>See Details</div><div class="btn-green apply">Apply</div></div>
        <div class="job"><span class="logo" style="display:block;background:#8b5cc7"></span><h5>UI/UX Designer</h5><div class="stars">★★★☆☆ <small>(4 Reviews)</small></div><div style="font-size:7px;margin-top:3px">● California, CA</div><div class="tags"><span>Full Time</span><span>Senior Level</span></div><div class="salary" style="margin-top:30px"><span><b>$3k</b>/Monthly</span>See Details</div><div class="btn-green apply off">Apply</div></div>
        <div class="job"><span class="logo" style="display:block;background:#e8a23a"></span><h5>Senior UI/UX<br>Designer</h5><div class="stars">★★★★☆ <small>(42 Reviews)</small></div><div style="font-size:7px;margin-top:3px">● California, CA</div><div class="tags"><span>Full Time</span><span>Senior Level</span><span>Remote</span></div><div class="salary"><span><b>$2.5k</b>/Monthly</span>See Details</div><div class="btn-green apply">Apply</div></div>
        <div class="job"><span class="logo" style="display:block;background:#8b5cc7"></span><h5>UI/UX Designer</h5><div class="stars">★★★☆☆ <small>(4 Reviews)</small></div><div style="font-size:7px;margin-top:3px">● California, CA</div><div class="tags"><span>Full Time</span><span>Senior Level</span></div><div class="salary" style="margin-top:30px"><span><b>$3k</b>/Monthly</span>See Details</div><div class="btn-green apply off">Apply</div></div>
      </div>
      <div class="filter">
        <div class="fh">Filter<span>Clear all</span></div>
        <h6>Job Type</h6>
        <div class="opt on"><i></i>Full Time</div><div class="opt"><i></i>Internship</div><div class="opt on"><i></i>Freelance</div><div class="opt"><i></i>Contractual</div>
        <h6>On Site/Remote</h6>
        <div class="opt on"><i></i>On Site</div><div class="opt"><i></i>Hybrid</div><div class="opt on"><i></i>Remote</div>
        <h6>Salary Range</h6>
        <div class="opt"><i></i>Under $ 1000</div><div class="opt"><i></i>$ 1000 – $ 5000</div><div class="opt"><i></i>$ 1000 – $ 2500</div><div class="opt on"><i></i>Above $ 2500</div>
        <h6>Others</h6>
        <div class="opt on"><i></i>On Site</div><div class="opt"><i></i>Hybrid</div><div class="opt on"><i></i>Remote</div>
      </div>
    </main>
    <div class="card activity">
      <div class="right-head">Last Activites<span>See All</span></div>
      <div class="act"><span class="ic" style="background:#87c032"></span><span>Your Application has accept<br><b style="color:var(--ink);font-weight:500">3 Companies</b></span></div>
      <div class="act"><span class="ic" style="background:var(--red)"></span><span>Your Application has rejected<br><b style="color:var(--ink);font-weight:500">1 Companies</b></span></div>
    </div>
    <div class="card skills">
      <h4>Skills</h4>
      <div class="skill"><span>Photo Editing</span><div class="bar"><b style="width:87%"></b></div>87%</div>
      <div class="skill"><span>Vector Illustration</span><div class="bar"><b style="width:84%"></b></div>84%</div>
      <div class="skill"><span>Motion Graphics</span><div class="bar"><b style="width:55%"></b></div>55%</div>
      <div class="skill"><span>Video Editing</span><div class="bar"><b style="width:67%"></b></div>67%</div>
      <div class="skill"><span>Layout Design</span><div class="bar"><b style="width:48%"></b></div>48%</div>
      <div class="skill"><span>Prototyping</span><div class="bar"><b style="width:90%"></b></div>90%</div>
      <div class="skill"><span>Interface Design</span><div class="bar"><b style="width:31%"></b></div>31%</div>
      <div class="skill"><span>Office Suite</span><div class="bar"><b style="width:54%"></b></div>54%</div>
    </div>
  </section>
</div>

<div class="band-brand"><div class="brand"><span class="dot"></span>ZELVOR</div></div>
</body>
</html>
```